Business Card and Simple Logo Desgin

New Zealand based start up company "Vesta Advisory LTD" requires business cards and simple logo design.

Card Content.

Vesta Advisory LTD

Rebecca Thornbury
CA, BMS (Hons)

r.thornbury@vestaadvisory.co.nz
PH +64 21 574 613

Target Market(s)

Corporate Business in IT, Finance and accounting.

Industry/Entity Type

Business

```html
<!DOCTYPE html>
<html lang="en">
<head>
<meta charset="utf-8">
<title>Vesta Advisory LTD — Business Card</title>
<link href="https://fonts.googleapis.com/css2?family=PT+Sans:wght@400;700&display=swap" rel="stylesheet">
<style>
  :root {
    --backdrop: #2a2a2a;
    --card-white: #ffffff;
    --card-shade: #e9e9e9;
    --accent-cyan: #00aee6;
    --band-indigo: #2e3192;
    --ink-dark: #231f20;
    --ink-grey: #5a5a5a;
    --ink-light: #ffffff;
  }
  * { margin: 0; padding: 0; box-sizing: border-box; }
  html, body {
    width: 1200px;
    height: 900px;
    overflow: hidden;
    background: var(--backdrop);
    font-family: "PT Sans", sans-serif;
  }
  .stage {
    position: relative;
    width: 1200px;
    height: 900px;
  }
  .business-card {
    position: absolute;
    left: 150px;
    top: 193px;
    width: 900px;
    height: 514px;
    border-radius: 18px;
    overflow: hidden;
    background: linear-gradient(160deg, var(--card-white) 35%, var(--card-shade) 100%);
  }
  .corner-accent {
    position: absolute;
    top: 0;
    right: 0;
    width: 420px;
    height: 230px;
    background: linear-gradient(200deg, var(--accent-cyan) 0%, rgba(0, 174, 230, 0.55) 45%, rgba(0, 174, 230, 0) 100%);
  }
  .brand {
    position: absolute;
    left: 60px;
    top: 62px;
    display: flex;
    align-items: center;
    gap: 16px;
  }
  .brand-square {
    width: 34px;
    height: 34px;
    background: var(--band-indigo);
  }
  .brand-name {
    font-weight: 700;
    font-size: 44px;
    line-height: 1;
    color: var(--ink-dark);
  }
  .holder {
    position: absolute;
    left: 60px;
    top: 232px;
  }
  .holder-name {
    font-size: 42px;
    color: var(--ink-grey);
    line-height: 1.15;
  }
  .holder-credentials {
    font-size: 28px;
    color: var(--ink-grey);
    margin-top: 6px;
  }
  .contact-band {
    position: absolute;
    left: 0;
    right: 0;
    bottom: 0;
    height: 160px;
    background: var(--band-indigo);
    padding: 34px 60px 0;
    color: var(--ink-light);
    font-size: 27px;
    line-height: 1.55;
  }
</style>
</head>
<body>
  <main class="stage">
    <section class="business-card" aria-label="Vesta Advisory LTD business card">
      <div class="corner-accent" role="img" aria-label="Decorative cyan accent area in the top-right corner"></div>

      <div class="brand">
        <span class="brand-square"></span>
        <span class="brand-name">Vesta Advisory</span>
      </div>

      <div class="holder">
        <p class="holder-name">Rebecca Thornbury</p>
        <p class="holder-credentials">CA, BMS (Hons)</p>
      </div>

      <div class="contact-band">
        <p class="contact-phone">PH +64 21 574 613</p>
        <p class="contact-email">r.thornbury@vestaadvisory.co.nz</p>
      </div>
    </section>
  </main>
</body>
</html>
```